Meridale Partners Website

Meridale Partners (MP) provide Analytics & Enterprise Performance Management (EPM) advisory & consultancy services. We are passionate about data and making a difference for our clients by working in partnership with them, helping them on their journey to becoming an Meridale Partner. We deliver insights which give our clients a competitive edge and a much deeper understanding of their organisation.

We need a website which shows who we are, what we do and how we do it.

www.meridale-partners.example is our very basic website at the moment. We want to completely revamp it with a corporate look

```html
<!DOCTYPE html>
<html lang="en">
<head>
<meta charset="utf-8">
<title>Meridale Partners</title>
<link href="https://fonts.googleapis.com/css2?family=Roboto:wght@400;500;700;900&display=swap" rel="stylesheet">
<style>
:root{
  --navy:#1d4a63;
  --navy-dark:#163a4f;
  --orange:#d4681f;
  --ink:#111;
  --text:#555;
  --pale:#eef3f7;
  --footer:#0c0e11;
  --white:#fff;
}
*{margin:0;padding:0;box-sizing:border-box}
html,body{width:1200px;height:4057px;overflow:hidden;background:var(--white)}
body{font-family:'Roboto',sans-serif;color:var(--text);position:relative}
.abs{position:absolute}
.btn{position:absolute;display:flex;align-items:center;justify-content:center;gap:10px;border-radius:30px;font-weight:700;font-size:15px;letter-spacing:1.5px;text-transform:uppercase;color:var(--white)}
.btn-orange{background:var(--orange)}
.btn-outline{border:2px solid var(--white)}
.arrow-dot{width:14px;height:14px}

/* header */
.site-header{position:absolute;top:0;left:0;width:1200px;height:76px;background:var(--white);z-index:5}
.brand{position:absolute;left:110px;top:14px;display:flex;align-items:center;gap:10px}
.brand-mark{width:46px;height:46px;border-radius:50%;background:var(--navy)}
.brand-name{font-weight:700;font-size:16px;line-height:18px;color:var(--navy);text-transform:uppercase}
.main-nav{position:absolute;left:326px;top:27px;display:flex;gap:28px;font-size:15px;letter-spacing:1.4px;color:#333;text-transform:uppercase}
.main-nav .active{color:var(--navy);border-bottom:2px solid var(--navy);padding-bottom:3px}
.login{left:958px;top:16px;width:129px;height:39px}

/* hero */
.hero{position:absolute;top:76px;left:0;width:1200px;height:735px;background:linear-gradient(160deg,#3d6f98 0%,#8fb3cf 35%,#cfdfea 55%,#4c7ca4 80%,#2a5275 100%)}
.hero-title{position:absolute;width:1200px;text-align:center;color:var(--white);font-weight:700;text-transform:uppercase}
.hero-kicker{top:306px;font-size:31px;letter-spacing:5px}
.hero-head{top:379px;font-size:41px;letter-spacing:5px}
.hero-cta{left:504px;top:457px;width:190px;height:47px}
.hero-curve{position:absolute;left:0;top:660px;width:1200px;height:160px}
.dots{position:absolute;top:707px;left:565px;display:flex;gap:10px;align-items:center}
.dots span{width:12px;height:12px;border-radius:50%;background:var(--white)}
.dots .on{width:18px;height:18px;background:transparent;border:2px solid var(--white)}

/* section titles */
.section-title{position:absolute;width:1200px;text-align:center;font-weight:900;font-size:31px;letter-spacing:4px;color:var(--ink);text-transform:uppercase}
.section-title em{font-style:normal;color:var(--navy)}
.section-title::after{content:"";display:block;width:68px;height:4px;background:var(--navy);margin:10px auto 0}

/* services */
.service{position:absolute;width:300px;text-align:center}
.service-photo{width:271px;height:271px;border-radius:50%;margin:0 auto;border:5px solid var(--navy)}
.service-photo.orange{border-color:var(--orange)}
.service h3{margin-top:34px;font-size:15px;letter-spacing:1.6px;color:var(--navy);font-weight:700;text-transform:uppercase}
.service h3::after{content:"";display:block;width:50px;height:3px;background:var(--orange);margin:10px auto 0}
.service p{margin-top:18px;font-size:15px;line-height:23px;padding:0 6px}
.read-more{display:inline-flex;align-items:center;gap:10px;margin-top:14px;font-size:15px;font-weight:700;letter-spacing:1.5px;color:var(--orange)}

/* who we are */
.who{position:absolute;top:1490px;left:0;width:1200px;height:515px;background:var(--pale)}
.who h2{position:absolute;left:110px;top:56px;font-size:31px;font-weight:900;letter-spacing:4px;color:var(--ink)}
.who p{position:absolute;left:110px;top:124px;width:493px;font-size:15px;line-height:25.7px;text-align:justify;color:#333}
.who .learn{left:110px;top:408px;width:191px;height:46px}
.who-visual{position:absolute;left:704px;top:72px;width:370px;height:372px;border-radius:50%;background:radial-gradient(circle at 60% 45%,#5c6b78 0%,#2b323a 55%,#1a1e23 70%,var(--pale) 71%)}

/* how we do it */
.card{position:absolute;top:2172px;width:224px;height:280px;background:var(--white);box-shadow:0 4px 18px rgba(0,0,0,.08);text-align:center;padding-top:26px}
.card.featured{background:var(--navy)}
.card-icon{width:104px;height:58px;margin:0 auto}
.card h3{margin-top:26px;font-size:15px;letter-spacing:1.5px;font-weight:700;color:var(--navy);line-height:20px;text-transform:uppercase}
.card.featured h3,.card.featured p{color:var(--white)}
.card h3::after{content:"";display:block;width:30px;height:3px;background:var(--orange);margin:8px auto 0}
.card p{margin:12px auto 0;width:196px;font-size:14px;line-height:19.5px;color:#444}

/* contact band */
.cta-band{position:absolute;top:2555px;left:0;width:1200px;height:401px;background:linear-gradient(90deg,#244f68,#2a5670 60%,#35627c)}
.cta-band h2{position:absolute;top:86px;width:1200px;text-align:center;color:var(--white);font-size:31px;font-weight:900;line-height:36px;text-transform:uppercase}
.cta-band .rule{position:absolute;left:564px;top:170px;width:72px;height:4px;background:var(--white)}
.cta-band h4{position:absolute;top:200px;width:1200px;text-align:center;color:var(--white);font-size:23px;font-weight:700;text-transform:uppercase}
.call{left:410px;top:261px;width:181px;height:47px}
.contact-btn{left:606px;top:261px;width:183px;height:47px}

/* get in touch */
.touch{position:absolute;top:2956px;left:0;width:1200px;height:640px;background:linear-gradient(180deg,#f1f3f5,#e7eaed)}
.touch-photo{position:absolute;left:110px;top:88px;width:534px;height:435px;background:linear-gradient(135deg,#2d4c6a,#8a98a4 45%,#d8cbb2 75%,#6b5a44)}
.touch-frame{position:absolute;left:718px;top:103px;width:408px;height:387px;border:3px solid var(--orange)}
.touch-corner{position:absolute;left:968px;top:370px;width:128px;height:66px;border-right:8px solid var(--navy);border-bottom:8px solid var(--navy)}
.form-card{position:absolute;left:458px;top:136px;width:630px;height:423px;background:var(--white);padding:38px 34px}
.form-card h2{font-size:31px;font-weight:900;letter-spacing:4px;color:var(--ink)}
.form-card h2::after{content:"";display:block;width:44px;height:3px;background:var(--navy);margin-top:8px}
.field{position:absolute;width:250px}
.field label{display:block;font-size:15px;color:#222;font-weight:500}
.field .input{margin-top:14px;padding-bottom:8px;border-bottom:1px solid #ccc;font-size:13px;color:#999}
.field.wide{width:552px}
.send{position:absolute;right:36px;bottom:40px;width:28px;height:28px;border-radius:50%;background:var(--navy)}

/* footer */
.footer{position:absolute;top:3560px;left:0;width:1200px;height:497px}
.footer-curve{position:absolute;left:0;top:0;width:1200px;height:200px}
.footer-body{position:absolute;top:160px;left:0;width:1200px;height:337px;background:var(--footer)}
.f-brand{position:absolute;left:97px;top:3760px;display:flex;align-items:center;gap:14px}
.f-brand .brand-mark{width:70px;height:70px;background:var(--white)}
.f-brand .brand-name{color:var(--white);font-size:24px;line-height:27px}
.f-about{position:absolute;left:97px;top:3830px;width:250px;font-size:14px;line-height:21px;color:#ddd}
.f-badge{position:absolute;left:97px;top:3898px;width:230px;height:48px;border-radius:4px;background:#2a2e34}
.f-col{position:absolute;top:3723px;color:var(--white)}
.f-col h5{font-size:14px;font-weight:700;text-transform:uppercase;margin-bottom:18px}
.f-col li{list-style:none;font-size:15px;margin-bottom:17px;color:#eee}
.f-col li::before{content:"»";margin-right:12px}
.f-contact{position:absolute;left:857px;width:290px;display:flex;gap:12px;color:var(--white)}
.f-contact .ico{flex:none;width:26px;height:26px;border-radius:50%;border:1.5px solid var(--white);display:flex;align-items:center;justify-content:center}
.f-contact small{display:block;font-size:11px;font-weight:700}
.f-contact span{font-size:14px;line-height:19px}
.f-rule{position:absolute;left:92px;top:3983px;width:1018px;height:1px;background:#333}
.copyright{position:absolute;left:92px;top:4007px;font-size:13px;color:#ddd}
.social{position:absolute;top:3998px;width:30px;height:30px;border-radius:50%;border:1.5px solid var(--white)}
</style>
</head>
<body>

<header class="site-header">
  <div class="brand"><div class="brand-mark"></div><div class="brand-name">Meridale<br>Partners</div></div>
  <nav class="main-nav"><span class="active">Home</span><span>Who we are</span><span>What we do</span><span>How we do it</span><span>Contact us</span></nav>
  <div class="btn btn-orange login">Login
    <svg width="12" height="13" viewBox="0 0 12 13"><rect x="1" y="6" width="10" height="7" rx="1" fill="#fff"/><path d="M3 6V4a3 3 0 0 1 6 0v2" stroke="#fff" stroke-width="1.6" fill="none"/></svg>
  </div>
</header>

<section class="hero" role="img" aria-label="Glass office towers seen from below against a blue sky">
</section>
<div class="hero-title hero-kicker">Welcome to</div>
<div class="hero-title hero-head">Meridale Partners</div>
<div class="btn btn-orange hero-cta">Get started
  <svg class="arrow-dot" viewBox="0 0 14 14"><circle cx="7" cy="7" r="7" fill="#fff"/><path d="M5 4l3 3-3 3" stroke="#d4681f" stroke-width="2" fill="none"/></svg>
</div>
<svg class="hero-curve" viewBox="0 0 1200 160" preserveAspectRatio="none">
  <path d="M0 10 Q600 230 1200 10 L1200 160 L0 160Z" fill="#1d4a63"/>
  <path d="M0 60 Q600 245 1200 60 L1200 160 L0 160Z" fill="#fff"/>
</svg>
<div class="dots"><span></span><span class="on"></span><span></span></div>

<h2 class="section-title" style="top:867px">Our <em>Services</em></h2>

<div class="service" style="left:94px;top:955px">
  <div class="service-photo" role="img" aria-label="Team reviewing printed charts on a desk" style="background:linear-gradient(135deg,#dfe6ec,#8ea4b8 60%,#3c5a74)"></div>
  <h3>Advise &amp; Architect Services</h3>
  <p>Helping our customers understand the art of the possible and safeguarding their investments by overseeing</p>
  <div class="read-more">Read More <svg class="arrow-dot" viewBox="0 0 14 14"><circle cx="7" cy="7" r="7" fill="#d4681f"/><path d="M5 4l3 3-3 3" stroke="#fff" stroke-width="2" fill="none"/></svg></div>
</div>
<div class="service" style="left:439px;top:955px">
  <div class="service-photo orange" role="img" aria-label="Two colleagues working together at a computer" style="background:linear-gradient(135deg,#c9a27a,#7b5a3f 50%,#3a3f46)"></div>
  <h3>Optimise &amp; Manage</h3>
  <p>Working with the project management team, through each stage of the project, with clearly defined</p>
  <div class="read-more" style="text-decoration:underline">Read More <svg class="arrow-dot" viewBox="0 0 14 14"><circle cx="7" cy="7" r="7" fill="#d4681f"/><path d="M5 4l3 3-3 3" stroke="#fff" stroke-width="2" fill="none"/></svg></div>
</div>
<div class="service" style="left:785px;top:955px">
  <div class="service-photo" role="img" aria-label="Hands typing on a laptop with digital gear graphics" style="background:linear-gradient(135deg,#7fa2b8,#35566f 55%,#1a2d3c)"></div>
  <h3>Design &amp; Implement</h3>
  <p>Our Managed Services delivers proactive, on-demand support for EPM and Data Analytics environments:</p>
  <div class="read-more">Read More <svg class="arrow-dot" viewBox="0 0 14 14"><circle cx="7" cy="7" r="7" fill="#d4681f"/><path d="M5 4l3 3-3 3" stroke="#fff" stroke-width="2" fill="none"/></svg></div>
</div>

<section class="who">
  <h2>WHO WE ARE</h2>
  <p>Meridale Partners is an exciting start-up in the Data Analytics and EPM space.Founded in 2019, MP specialise in the implementation and support of BI, EPM and Data Analytics business solutions, both in the Cloud and on-premise.Lorem ipsum dolor sited amet, consectetur adipiscing elit, sed doed eiusmod tempor incididunt ut labore et dolore magna aliquad. Ut enim ad minim veniam, quis nostrud exercitation ullamco laboris nisi aliquip commodo consequated Duis aute irure dolor in reprehenderit in voluptate velit esse cillum dolore eu fugiat nulla pariatur. Excepteur sinted occaecat cupidatated culpa quied officia reprehenderit deserunted.mollit anim id est laborum</p>
  <div class="btn btn-orange learn">Learn more <svg class="arrow-dot" viewBox="0 0 14 14"><circle cx="7" cy="7" r="7" fill="#fff"/><path d="M5 4l3 3-3 3" stroke="#d4681f" stroke-width="2" fill="none"/></svg></div>
  <div class="who-visual" role="img" aria-label="Dark curved emblem filled with analytics dashboard imagery"></div>
</section>

<h2 class="section-title" style="top:2087px">How <em>we</em> <em style="color:#1d4a63">Do it</em></h2>

<div class="card" style="left:110px">
  <svg class="card-icon" viewBox="0 0 104 58"><path d="M6 52 A46 46 0 0 1 98 52" stroke="#d4681f" stroke-width="6" fill="none"/><circle cx="52" cy="52" r="38" fill="#1d4a63"/><rect x="38" y="30" width="28" height="20" fill="none" stroke="#fff" stroke-width="2"/><path d="M42 46v-6M48 46v-10M54 46v-4M60 46v-12" stroke="#fff" stroke-width="2"/></svg>
  <h3>Analytics</h3>
  <p>Sed ut perspiciatis unde omnis isted natust error sit voluptaac cusantiuim sited doloremque laudantium ut perspiciatis.</p>
</div>
<div class="card" style="left:362px">
  <svg class="card-icon" viewBox="0 0 104 58"><path d="M6 52 A46 46 0 0 1 98 52" stroke="#d4681f" stroke-width="6" fill="none"/><circle cx="52" cy="52" r="38" fill="#1d4a63"/><circle cx="52" cy="32" r="5" fill="none" stroke="#fff" stroke-width="2"/><path d="M40 52h24M44 52v-8h16v8" stroke="#fff" stroke-width="2" fill="none"/></svg>
  <h3>Advisory</h3>
  <p>Sed ut perspiciatis unde omnis isted natust error sit voluptaac cusantiuim sited doloremque laudantium ut perspiciatis.</p>
</div>
<div class="card featured" style="left:613px">
  <svg class="card-icon" viewBox="0 0 104 58"><path d="M6 52 A46 46 0 0 1 98 52" stroke="#d4681f" stroke-width="6" fill="none"/><circle cx="52" cy="52" r="38" fill="#fff"/><circle cx="60" cy="30" r="6" fill="none" stroke="#1d4a63" stroke-width="2"/><path d="M42 50v-6M48 50v-10M54 50v-4M60 50v-12M38 36h10" stroke="#1d4a63" stroke-width="2"/></svg>
  <h3>Performance<br>Managemen</h3>
  <p>Sed ut perspiciatis unde omnis isted natust error sit voluptaac laudantium ut perspiciatis.</p>
</div>
<div class="card" style="left:863px">
  <svg class="card-icon" viewBox="0 0 104 58"><path d="M6 52 A46 46 0 0 1 98 52" stroke="#d4681f" stroke-width="6" fill="none"/><circle cx="52" cy="52" r="38" fill="#1d4a63"/><rect x="38" y="30" width="28" height="20" fill="none" stroke="#fff" stroke-width="2"/><path d="M42 46v-6M48 46v-10M54 46v-4M60 46v-12" stroke="#fff" stroke-width="2"/></svg>
  <h3>Consultancy<br>Services</h3>
  <p>Sed ut perspiciatis unde omnis isted natust error sit voluptaac laudantium ut perspiciatis.</p>
</div>

<section class="cta-band" role="img" aria-label="Muted navy background of a laptop with business charts">
  <h2>Contact us to discuss your<br>business needs</h2>
  <div class="rule"></div>
  <h4>Advise &amp; Architect | Design &amp; Implement | Optimise &amp; Manage</h4>
  <div class="btn btn-orange call">01 555 0148
    <svg width="14" height="14" viewBox="0 0 14 14"><path d="M3 1l3 3-2 2a8 8 0 0 0 4 4l2-2 3 3-2 2C6 13 1 8 1 3z" fill="#fff"/></svg>
  </div>
  <div class="btn btn-outline contact-btn">Contact us <svg class="arrow-dot" viewBox="0 0 14 14"><circle cx="7" cy="7" r="7" fill="#fff"/><path d="M5 4l3 3-3 3" stroke="#1d4a63" stroke-width="2" fill="none"/></svg></div>
</section>

<section class="touch">
  <div class="touch-photo" role="img" aria-label="Businessmen analysing charts on a desk and monitor"></div>
  <div class="touch-frame"></div>
  <div class="touch-corner"></div>
  <div class="form-card">
    <h2>GET IN TOUCH</h2>
    <div class="field" style="left:34px;top:112px"><label>Enter Name:</label><div class="input">Sam Carter</div></div>
    <div class="field" style="left:334px;top:112px"><label>Enter Email:</label><div class="input">sam@carter.example</div></div>
    <div class="field" style="left:34px;top:198px"><label>Address:</label><div class="input">Sam Carter</div></div>
    <div class="field" style="left:334px;top:198px"><label>Phone:</label><div class="input">+1 555 010 0000</div></div>
    <div class="field wide" style="left:34px;top:284px"><label>Message:</label><div class="input" style="margin-top:44px">Lorem ipsum dolor sit amet</div></div>
    <svg class="send" viewBox="0 0 28 28"><circle cx="14" cy="14" r="14" fill="#1d4a63"/><path d="M7 14l13-6-4 13-3-5z" fill="#fff"/></svg>
  </div>
</section>

<footer class="footer">
  <svg class="footer-curve" viewBox="0 0 1200 200" preserveAspectRatio="none">
    <path d="M0 140 Q600 -60 1200 140 L1200 200 L0 200Z" fill="#1d4a63"/>
    <path d="M0 165 Q600 -20 1200 165 L1200 200 L0 200Z" fill="#0c0e11"/>
  </svg>
  <div class="footer-body"></div>
</footer>
<div class="f-brand"><div class="brand-mark"></div><div class="brand-name">Meridale<br>Partners</div></div>
<p class="f-about">Meridale Partners is an exciting start-up in the Data Analytics and EPM space.</p>
<div class="f-badge"></div>
<div class="f-col" style="left:438px"><h5>Quicklinks</h5><ul><li>Home</li><li>Who we are</li><li>What we do</li><li>How we do it</li><li>Contact Us</li></ul></div>
<div class="f-col" style="left:633px"><h5>Otherlinks</h5><ul><li>FAQ</li><li>Legal Information</li><li>Terms &amp; Condition</li><li>Privacy Policy</li><li>Support</li></ul></div>
<div class="f-col" style="left:857px"><h5>Contact us</h5></div>
<div class="f-contact" style="top:3766px"><div class="ico"><svg width="12" height="12" viewBox="0 0 14 14"><path d="M3 1l3 3-2 2a8 8 0 0 0 4 4l2-2 3 3-2 2C6 13 1 8 1 3z" fill="#fff"/></svg></div><div><small>Phone</small><span>01 555 0148</span></div></div>
<div class="f-contact" style="top:3825px"><div class="ico"><svg width="10" height="13" viewBox="0 0 10 13"><path d="M5 12S1 7 1 4.5a4 4 0 0 1 8 0C9 7 5 12 5 12z" fill="none" stroke="#fff" stroke-width="1.5"/><circle cx="5" cy="4.5" r="1.4" fill="#fff"/></svg></div><div><small>Location</small><span>12 Harbour Row, Eastgate,<br>Kilmore 4, K04 PX21</span></div></div>
<div class="f-contact" style="top:3896px"><div class="ico"><svg width="12" height="12" viewBox="0 0 14 14"><path d="M3 1l3 3-2 2a8 8 0 0 0 4 4l2-2 3 3-2 2C6 13 1 8 1 3z" fill="#fff"/></svg></div><div><small>Email</small><span>info@meridale-partners.example</span></div></div>
<div class="f-rule"></div>
<p class="copyright">2022 Copyright Meridale Partners All Rights Reserved.</p>
<div class="social" style="left:1027px"></div>
<div class="social" style="left:1067px"></div>

</body>
</html>
```